New Business Card Design Project LORVANTI-Italy

we are LORVANTI-Italy
our company in the market for 3 years we are luxury cosmetic company and its about time for a facelift :)
i will like to have elegant luxurious and unique business card
that will give the person that get it a unique, luxurious and elegant impression
I'm VERY OPEN FOR NEW IDEAS , even duo i add a few files of things that i see on line and i like them

i add my logo as well
my website is LORVANTI.COM
(if you would like to see the main style that we have)

Target Market(s)

adult that have money :)

Industry/Entity Type

Business

Contact Information for Business Card

Name - Dario Lorvanti
Position - CEO and CO Founder
address - 4817 E Halvern
telephone - 555-384-1926
email - dario@lorvanti.com
fax - 555-384-1926
website - LORVANTI.COM

Colors
000000
959595
fbee3e
ffffff

Requirements
Must have
• big logo in GOLD color
• elegant look
• impressive
Nice to have
• not must but maybe classy pattern background
• not must but maybe emblem
• maybe clear plastic business card
Should not have
• colors
• images

```html
<!DOCTYPE html>
<html lang="en">
<head>
<meta charset="utf-8">
<title>Dario Lorvanti – Business Card</title>
<link rel="stylesheet" href="https://fonts.googleapis.com/css2?family=Tinos&display=swap">
<style>
  :root {
    --card-dark: #141414;
    --card-mid: #262626;
    --gold: #fbee3e;
    --gold-soft: #fff7a0;
    --gold-faint: rgba(180, 150, 70, 0.16);
    --silver: #d6d6d6;
    --silver-light: #f2f2f2;
  }
  html, body {
    margin: 0;
    padding: 0;
    width: 686px;
    height: 1200px;
    overflow: hidden;
    background: #000;
  }
  .card {
    position: relative;
    width: 686px;
    height: 1200px;
    background: radial-gradient(ellipse at 50% 35%, var(--card-mid) 0%, var(--card-dark) 75%);
    font-family: "Tinos", "Times New Roman", serif;
    overflow: hidden;
  }
  .card-frame {
    position: absolute;
    left: 40px;
    top: 40px;
    width: 600px;
    height: 1114px;
    border: 3px solid var(--gold);
  }
  .emblem-area {
    position: absolute;
    left: 101px;
    top: 274px;
    width: 480px;
    height: 480px;
  }
  .identity {
    position: absolute;
    left: 0;
    right: 0;
    top: 462px;
    text-align: center;
  }
  .identity-name {
    margin: 0;
    font-size: 80px;
    font-weight: 400;
    line-height: 1;
    background: linear-gradient(180deg, var(--gold) 0%, var(--gold-soft) 100%);
    -webkit-background-clip: text;
    background-clip: text;
    color: transparent;
  }
  .identity-role {
    margin: 10px 0 0;
    font-size: 25px;
    color: var(--gold-soft);
  }
  .contact {
    position: absolute;
    left: 0;
    right: 0;
    top: 1004px;
    margin: 0;
    padding: 0;
    list-style: none;
    text-align: center;
    font-size: 29px;
    letter-spacing: 1.5px;
    line-height: 41px;
    color: var(--silver);
  }
</style>
</head>
<body>
  <main class="card">
    <svg class="emblem-area" viewBox="0 0 480 480" role="img" aria-label="Faint brand emblem area">
      <circle cx="240" cy="240" r="232" fill="none" stroke="var(--gold-faint)" stroke-width="10"/>
    </svg>
    <div class="card-frame"></div>
    <header class="identity">
      <h1 class="identity-name">Dario Lorvanti</h1>
      <p class="identity-role">CEO and CO Founder</p>
    </header>
    <ul class="contact">
      <li class="contact-address">4817 E Halvern</li>
      <li class="contact-phone">555-384-1926</li>
      <li class="contact-email">dario@lorvanti.com</li>
    </ul>
  </main>
</body>
</html>
```